Community Management Company in need of WordPress templates for website redesign

We are a community association management company providing services to homeowner associations (HOAs), condominium associations, cooperatives, municipal utility districts, luxury high-rises and large master-planned communities within the Real Estate category.

We are looking to do a refresh of our site with newly-designed pages that are compatible with WordPress and can be uploaded to a domain with little complications.

We are interested in first having a landing page designed based on a specific audience and call to actions as described in the design brief file attached to this design project and pasted below:
Design Brief for HavenStead Website Refresh

General Details:
Company Name: HavenStead
Business Location: Carrollton, TX – HQ
Current website: www.havenstead-example.com

Overview:

We are looking to for a refresh of our site with newly-designed pages that are compatible with WordPress and can be uploaded to a domain with little complications.

Our target audience / target market:
HOA and Association Board Members, Real Estate Builders & Developers, Residents and Homeowners, Vendors, Potential Business Partners

Project scope:
Create a landing page template with the target audience of HOA Board Members who are prospects of HavenStead
The goal of the landing page is to have them fill out the proposal form by having the page take them from our “why” message to our “how” and “what” messages so they are compelled to fill out the form. The new landing page needs to drive that behavior.
Our messages will include the following

Why messages:
• Because you deserve an exceptional community
• Because you and your residents deserve an exceptional lifestyle
• Because your community matters
• Because your residents matter
• Exceptional Community. Managed
• Exceptional Lifestyle. Delivered
How/What messages:

With over 25 years of experience, HavenStead provides exceptional community management solutions with the transparency and visibility your community deserves. Our fully integrated services are provided at competitive prices with the best people, best practices, and best cloud-based and mobile app technology.

Our team is made up of the industry’s leading experts equipped to answer your questions quickly. Our team includes: certified managers, degreed and certified accountants, experienced, multi-lingual customer service representatives, technology staff and industry executives. We perform industry leading best practices, on behalf of the communities we serve, ensuring you receive the highest level support, guidance and tools to assist in performing your fiduciary duties. With our proprietary, cloud-based and mobile app technology, pertinent community information is at your fingertips. You will be empowered to manage the business affairs of your community anytime, from any device, anywhere.

Our community management services include personalized onsite management, portfolio management, full-service community maintenance services, community management for builders and property developers, and Virtual CAM (Community Association Manager) management.

Our community communication services include cloud-based board, resident, closing, and attorney portals and mobile app technology, providing the transparency and visibility into the business affairs that your community deserves. In addition, we provide several communication tools to keep homeowners and residents informed via our community website, newsletter and event services.

HavenStead, one of the largest and fastest growing community management companies, is proud to provide exceptional services to hundreds of community associations from under 50 units to over 7,000 units in Arizona, California, Colorado, Florida, Georgia, Louisiana, Nevada, North Carolina, Oregon, Texas and Washington, including homeowner associations (HOAs), condominium associations, cooperatives, luxury high-rises, municipal utility districts and large master-planned communities.

Other page elements: additional content block/placeholders for:
• Link to Service description and technology pages
• Link to Mobile Apps page
• Request a proposal form fill content block
• Find an office form fill content block and link to local page upon completion of search via zip or state
• Contact us content block with information to include phone, email, fax, etc. and link to contact us landing page

Template Elements:
Files will also be uploaded including:
• Logo
• Colors
• Sales PPT for their reference

Please see attached design brief (file #4), logos (file #2&3), colors & branding standards (file #5) and a sales PPT deck (file #1) geared towards the audience for your reference.
Updates

Reason: I am extending the deadline by one week to give everyone a chance to provide updates based on the feedback and submissions. Thank you for all of your efforts. I look forward to seeing all of your designs.

Reason: Good day everyone, We are extending our deadline by one more week; so please continue to submit your designs and revisions. We look forward to seeing your work. Regards.

Thank you for all of your submissions.  I am in the process of getting votes tallied and should have some further information Tuesday of next week.

I am currently reviewing the votes and comments from the poll and will provide feedback within the next day; so please stay tuned.

We are conducting one more round of voting for the website refresh.  Once this is complete we will contact the finalists and make a selection shortly thereafter.  Thank you again for your participation.  Please stay tuned.

We are finalizing our 2nd poll and will request revisions, if appropriate.  Thank you.

Target Market(s)

HOA Board members per the design brief

Industry/Entity Type

Communication

Requirements
Must have
• focus on a landing page first; not the homepage design
Nice to have
• Please see design brief - File #4
Should not have
• home page elements for the time being.

```html
<!DOCTYPE html>
<html lang="en">
<head>
<meta charset="utf-8">
<title>HavenStead – Exceptional Community Management</title>
<link href="https://fonts.googleapis.com/css2?family=Ubuntu:ital,wght@0,300;0,400;0,500;0,700;1,400;1,500&display=swap" rel="stylesheet">
<style>
:root{
  --teal:#1f7286;
  --teal-dark:#145466;
  --teal-deep:#0f4656;
  --field:#2a8196;
  --field-line:#3c95aa;
  --green:#4c7a24;
  --ink:#1c1c1c;
  --body:#3a3a3a;
  --muted:#707070;
  --footer-bg:#f1f1f1;
  --white:#ffffff;
}
*{box-sizing:border-box;margin:0;padding:0}
html,body{width:1200px;height:2521px;overflow:hidden}
body{position:relative;background:var(--white);font-family:"Ubuntu",sans-serif;color:var(--body)}

/* Hero */
.hero-photo{position:absolute;left:0;top:0;width:1200px;height:700px;
  background:linear-gradient(180deg,#9cc3e0 0%,#c9dcea 35%,#e9e4dc 65%,#f2ece4 100%)}
.brand{position:absolute;left:141px;top:34px}
.brand-name{font-size:60px;font-weight:700;color:var(--teal-dark);letter-spacing:-1px;line-height:1}
.brand-sub{font-size:12px;color:var(--teal-dark);text-align:right;margin-top:2px;letter-spacing:1px}

.office-finder{position:absolute;left:141px;top:517px;width:335px;height:168px;background:var(--white);
  box-shadow:0 2px 8px rgba(0,0,0,.25)}
.office-finder-head{background:var(--teal-dark);padding:14px 14px 12px;height:104px}
.office-finder-title{color:var(--white);font-size:18px;font-weight:500;text-transform:uppercase;letter-spacing:.3px}
.office-finder-text{color:#d6eaf0;font-size:13px;line-height:18px;margin-top:6px}
.office-finder-form{display:flex;gap:10px;padding:14px 14px}
.zip-input{flex:1;height:38px;border:1px solid #cfcfcf;font:13px "Ubuntu",sans-serif;color:#999;padding:0 10px;display:flex;align-items:center}
.zip-submit{width:96px;height:38px;background:var(--teal-dark);color:var(--white);font-size:14px;font-weight:700;display:flex;align-items:center;justify-content:center}

/* Why band */
.why-band{position:absolute;left:0;top:640px;width:1200px;height:255px}
.why-band svg{position:absolute;left:0;top:0}
.why-title{position:absolute;left:0;top:88px;width:1200px;text-align:center;color:var(--white);text-transform:uppercase;font-weight:700}
.why-title .lead{display:block;font-size:42px;letter-spacing:1px}
.why-title .strong{display:block;font-size:68px;line-height:82px;letter-spacing:1px}
.why-pointer{position:absolute;left:582px;top:894px}

/* Story */
.story{position:absolute;left:141px;top:928px;width:1032px;font-size:15px;line-height:21px;color:var(--body)}
.story p{margin-bottom:21px}

/* Features */
.feature{position:absolute;top:1466px;width:445px}
.feature-services{left:141px}
.feature-apps{left:628px}
.feature h2{font-size:29px;font-weight:700;color:var(--ink);text-transform:uppercase;margin-bottom:10px}
.feature p{font-size:14px;line-height:21px;color:var(--body);height:196px}
.read-more{display:inline-block;width:102px;height:31px;line-height:31px;background:var(--green);color:var(--white);font-size:13px;text-align:center;text-transform:uppercase}

/* Proposal */
.proposal{position:absolute;left:0;top:1782px;width:1200px;height:474px;
  background:linear-gradient(180deg,#2c7f93 0%,#1d6a7e 40%,#155869 100%)}
.proposal-photo{position:absolute;inset:0;background:radial-gradient(ellipse at 60% 30%,rgba(255,255,255,.14),rgba(255,255,255,0) 60%)}
.proposal h2{position:absolute;left:141px;top:36px;color:var(--white);font-size:26px;font-weight:500;text-transform:uppercase}
.field{position:absolute;height:32px;background:var(--field);border:1px solid var(--field-line);color:#cfe7ee;font-size:12px;padding:0 10px;display:flex;align-items:center}
.field.select::after{content:"";position:absolute;right:0;top:0;width:28px;height:30px;background:var(--teal-deep)}
.field.select::before{content:"";position:absolute;right:9px;top:13px;border:5px solid transparent;border-top-color:#cfe7ee;z-index:1}
.field.area{align-items:flex-start;padding-top:8px}
.community-title{position:absolute;left:141px;top:302px;color:var(--white);font-size:17px;font-style:italic;font-weight:500}
.proposal-submit{position:absolute;left:961px;top:398px;width:96px;height:32px;background:var(--green);color:var(--white);font-size:13px;display:flex;align-items:center;justify-content:center;text-transform:uppercase}

/* Contact */
.contact{position:absolute;left:0;top:2256px;width:1200px;height:227px;background:var(--footer-bg)}
.contact h3{position:absolute;left:141px;top:34px;font-size:17px;font-style:italic;font-weight:500;color:var(--ink)}
.contact-hours{position:absolute;left:141px;top:70px;font-size:13px;color:var(--muted)}
.contact-list{position:absolute;left:141px;top:100px;font-size:12px;line-height:29px;list-style:none}
.contact-list b{display:inline-block;width:70px;color:#444;font-weight:700}
.contact-list span{color:#8b9aa8}
.contact-brand{position:absolute;left:865px;top:40px;font-size:44px;font-weight:700;color:#8a8a8a;letter-spacing:-1px}
.social{position:absolute;left:863px;top:112px;display:flex;gap:6px}
.social i{display:block;width:28px;height:28px;background:#3d3d3d}

.legal{position:absolute;left:0;top:2483px;width:1200px;height:38px;background:var(--teal);color:#d9edf2;font-size:12px;text-align:center;line-height:38px}
</style>
</head>
<body>

<div class="hero-photo" role="img" aria-label="Photo of a smiling young family lying together in front of their home"></div>

<div class="brand">
  <div class="brand-name">HavenStead</div>
  <div class="brand-sub">POWERED BY NEXALINK</div>
</div>

<div class="why-band">
  <svg width="1200" height="255" viewBox="0 0 1200 255" aria-hidden="true">
    <path d="M0 28 C300 -10 560 50 820 30 C1000 16 1120 10 1200 22 L1200 255 L0 255 Z" fill="#1f7286"/>
    <path d="M0 40 C300 2 560 62 820 42 C1000 28 1120 22 1200 34 L1200 255 L0 255 Z" fill="#1a6779"/>
  </svg>
  <h1 class="why-title"><span class="lead">Because you deserve an</span><span class="strong">Exceptional Community</span></h1>
</div>
<svg class="why-pointer" width="36" height="18" viewBox="0 0 36 18" aria-hidden="true"><path d="M0 0 H36 L18 18 Z" fill="#1a6779"/></svg>

<div class="office-finder">
  <div class="office-finder-head">
    <div class="office-finder-title">Find a HavenStead Office</div>
    <div class="office-finder-text">Find a HavenStead office nearest you by entering your zip code</div>
  </div>
  <div class="office-finder-form">
    <div class="zip-input">Zip Code</div>
    <div class="zip-submit">SUBMIT</div>
  </div>
</div>

<section class="story">
  <p>With over 25 years of experience, HavenStead provides exceptional community management solutions with the transparency and visibility your community deserves. Our fully integrated services are provided at competitive prices with the best people, best practices, and best cloud-based and mobile app technology.</p>
  <p>Our team is made up of the industry’s leading experts equipped to answer your questions quickly. Our team includes: certified managers, degreed and certified accountants, experienced, multi-lingual customer service representatives, technology staff and industry executives. We perform industry leading best practices, on behalf of the communities we serve, ensuring you receive the highest level support, guidance and tools to assist in performing your fiduciary duties. With our proprietary, cloud-based and mobile app technology, pertinent community information is at your fingertips. You will be empowered to manage the business affairs of your community anytime, from any device, anywhere.</p>
  <p>Our community management services include personalized onsite management, portfolio management, full-service community maintenance services, community management for builders and property developers, and Virtual CAM (Community Association Manager) management.</p>
  <p>Our community communication services include cloud-based board, resident, closing, and attorney portals and mobile app technology, providing the transparency and visibility into the business affairs that your community deserves. In addition, we provide several communication tools to keep homeowners and residents informed via our community website, newsletter and event services.</p>
  <p>HavenStead, one of the largest and fastest growing community management companies, is proud to provide exceptional services to hundreds of community associations from under 50 units to over 7,000 units in Arizona, California, Colorado, Florida, Georgia, Louisiana, Nevada, North Carolina, Oregon, Texas and Washington, including homeowner associations (HOAs), condominium associations, cooperatives, luxury high-rises, municipal utility districts and large master-planned communities.</p>
</section>

<section class="feature feature-services">
  <h2>Services</h2>
  <p>Our HOA management services are a unique set of capabilities that include a bundle of services that are all fully integrated into our best people, best practices and best technology approach to managing your community to ensure the fullest possible community development. Our HOA management services enhance your level of community development, a concept we define as when a community operates at its peak potential in terms of financial and operational aspects as well as a deep sense of community spirit.</p>
  <span class="read-more">Read more</span>
</section>
<section class="feature feature-apps">
  <h2>Mobile Apps</h2>
  <p>Lorem Ipsum is simply dummy text of the printing and typesetting industry. Lorem Ipsum has been the industry's standard dummy text ever since the 1500s, when an unknown printer took a galley of type and scrambled it to make a type specimen book. It has survived not only five centuries, but also the leap into electronic typesetting, remaining essentially unchanged. It was popularised in the 1960s with the release of transfer sheets containing Lorem Ipsum.</p>
  <span class="read-more">Read more</span>
</section>

<section class="proposal">
  <div class="proposal-photo" role="img" aria-label="Faint photo of a suburban home behind the proposal form"></div>
  <h2>Request a Proposal</h2>
  <div class="field" style="left:141px;top:84px;width:451px">First Name:</div>
  <div class="field" style="left:605px;top:84px;width:214px">City:</div>
  <div class="field" style="left:835px;top:84px;width:222px">State/Province:</div>
  <div class="field" style="left:141px;top:125px;width:451px">Last Name:</div>
  <div class="field" style="left:605px;top:125px;width:214px">Email:</div>
  <div class="field" style="left:835px;top:125px;width:222px">Confirm Email:</div>
  <div class="field" style="left:141px;top:166px;width:451px">Title:</div>
  <div class="field" style="left:605px;top:166px;width:214px">Phone:</div>
  <div class="field" style="left:835px;top:166px;width:222px">Best time to contact:</div>
  <div class="field area" style="left:141px;top:207px;width:451px;height:74px">Address:</div>
  <div class="field select" style="left:605px;top:207px;width:452px">How did you hear about us?</div>
  <div class="field" style="left:605px;top:249px;width:452px">Name of Referral Source</div>
  <div class="community-title">Community Information</div>
  <div class="field" style="left:141px;top:352px;width:451px">Name of Community:</div>
  <div class="field select" style="left:605px;top:352px;width:452px">Type of Community:</div>
  <div class="field" style="left:141px;top:393px;width:451px">Of Homes:</div>
  <div class="proposal-submit">Submit</div>
</section>

<footer class="contact">
  <h3>Contact Us</h3>
  <p class="contact-hours">We are open from 7:30 a.m. - 7:00 p.m. Central time, Monday through Friday.</p>
  <ul class="contact-list">
    <li><b>PHONE:</b><span>866-555-0142 (866-555-0143)</span></li>
    <li><b>FAX:</b><span>866-555-0199</span></li>
    <li><b>EMAIL:</b><span>SERVICE@HAVENSTEAD-EXAMPLE.COM</span></li>
  </ul>
  <div class="contact-brand">HavenStead</div>
  <div class="social" aria-label="Social links"><i></i><i></i><i></i><i></i><i></i><i></i></div>
</footer>
<div class="legal">© 2014 HavenStead LLC. All rights reserved.</div>

</body>
</html>
```